New business card, letter head, email signature and Portfolio for our Security company.

We are an Crest security company that provides a top quality manpower services to protect high rise buildings, retail and all type of properties and would like a new business card/logo look.

- We would like the spot UV design.
- Matt black (double sided).
- We would like to incorporate a royal blue colour (feel free to experiment with it).
- Feel free to try different lengths with the card to make it stand out more than a normal business card.
- We would like the logo to be an eagle eye in the background (shines when card is tilted slightly in the background, either on the front, back or both sides of the card). Image attached as an example of eye shape (colour to be either black or royal blue).
- HARBOUR CREST SECURITY SERVICES PTY. LTD. and HCSS to be placed on one side of the card and on the other side of the card to have;

- Name in slightly bigger font than the position (directly on the bottom on the name).
- Mobile number
- Email address
- Website email address
- PO BOX address

Can we please have the files in a format that we can edit.

Reason: I need to consult my business partner with the designs so far and will make a decision from there.

Target Market(s)

Security Industry

Industry/Entity Type

Business

Contact Information for Business Card

- Mobile number
- Email address
- Website email address
- PO BOX address

Logo Text

HCSS and underneath the HCSS please add HARBOUR CREST SECURITY SERVICES PTY. LTD.

Font styles to use
Other font styles liked:
• bold type font

Colors
0255a3
000000

Requirements
Must have
• We are an Crest security company that provides a top quality manpower services to protect high rise buildings, retail and all type of properties and would like a new business card/logo look.
• - We would like the spot UV design.
• - Matt black (double sided).
• - We would like to incorporate a royal blue colour (feel free to experiment with it).
• - Feel free to try different lengths with the card to make it stand out more than a normal business card.
• - We would like the logo to be an eagle eye in the background (shines when card is tilted slightly in the background, either on the front, back or both sides of the card). Image attached as an example of eye shape (colour to be either black or royal blue).
• - HARBOUR CREST SECURITY SERVICES PTY. LTD. and HCSS to be placed on one side of the card and on the other side of the card to have;
• - Name in slightly bigger font than the position (directly on the bottom on the name).
• - Mobile number
• - Email address
• - Website email address
• - PO BOX address
• Can we please have the files in a format that we can edit.
Nice to have
• Feel free to try different lengths with the card to make it stand out more than a normal business card.
• Please find "URBAN JUNGLE" font attached and incorporate HCSS into the same style with building's inside the HCSS bold front also add HARBOUR into the bottom part of the S and follow on E - Crest on the bottom S - SECURITY on the bottom S - SERVICES on the bottom of each letter.
• other than that, I'll be happy with a bold modern font for the HCSS and HARBOUR CREST SECURITY SERVICES in a bold and thinner font underneath.

```html
<!DOCTYPE html>
<html lang="en">
<head>
<meta charset="utf-8">
<title>Harbour Crest Security Services – Business Card</title>
<link href="https://fonts.googleapis.com/css2?family=Montserrat:wght@400;600;800&display=swap" rel="stylesheet">
<style>
  :root {
    --backdrop: #9c6136;
    --matt-black: #000000;
    --royal-blue: #0255a3;
    --type-blue: #1f5fb0;
    --eye-grey: #3a3a3a;
    --ink-navy: #0a1a33;
    --white: #ffffff;
  }
  * { margin: 0; padding: 0; box-sizing: border-box; }
  html, body {
    width: 1200px; height: 400px; overflow: hidden;
    background: var(--backdrop);
    font-family: "Montserrat", sans-serif;
  }
  .stage { position: relative; width: 1200px; height: 400px; }
  .card {
    position: absolute; top: 93px;
    width: 479px; height: 213px;
    overflow: hidden;
  }
  .card--front { left: 109px; background: var(--matt-black); }
  .card--back { left: 611px; background: var(--royal-blue); }

  .eye-mark {
    position: absolute; left: 62px; top: 20px;
    width: 360px; height: 170px;
    border-radius: 50% 10% 60% 40%;
    background: radial-gradient(ellipse at 45% 45%, var(--eye-grey) 0%, #1c1c1c 55%, var(--matt-black) 100%);
  }
  .company-stack {
    position: absolute; left: 22px; top: 139px;
    color: var(--type-blue);
    font-weight: 600; font-size: 12.5px; line-height: 14px;
    letter-spacing: 0.2px; list-style: none;
  }

  .brand {
    position: absolute; left: 39px; top: 36px;
    color: var(--white);
  }
  .brand__initials {
    font-weight: 800; font-size: 58px; line-height: 60px; letter-spacing: 1px;
  }
  .brand__name {
    font-weight: 800; font-size: 8.5px; letter-spacing: 0.1px; margin-top: 2px;
  }
  .divider {
    position: absolute; left: 225px; top: 35px;
    width: 1px; height: 145px; background: var(--ink-navy);
  }
  .contact {
    position: absolute; left: 246px; top: 103px;
    list-style: none;
    font-size: 12.5px; line-height: 16.5px;
    color: var(--ink-navy);
  }
  .contact__name { color: var(--white); font-weight: 600; }
</style>
</head>
<body>
<main class="stage">
  <section class="card card--front">
    <div class="eye-mark" role="img" aria-label="Eagle eye emblem in spot UV grey on matt black"></div>
    <ul class="company-stack">
      <li>HARBOUR</li>
      <li>CREST</li>
      <li>SECURITY</li>
      <li>SERVICES</li>
    </ul>
  </section>

  <section class="card card--back">
    <div class="brand">
      <div class="brand__initials">HCSS</div>
      <div class="brand__name">HARBOUR CREST SECURITY SERVICES</div>
    </div>
    <div class="divider"></div>
    <ul class="contact">
      <li class="contact__name">JORDAN MERCER</li>
      <li>MOBILE NUMBER</li>
      <li>EMAIL ADDRESS</li>
      <li>WEBSITE EMAIL ADDRESS</li>
      <li>PO BOX ADDRESS</li>
    </ul>
  </section>
</main>
</body>
</html>
```